Estate Planning Law Firm opening new branch in Florida

I am an experienced estate planning attorney that recently relocated to Florida. Looking for a banner Ad to place on platforms such as HomeLane, Chatterbox and Picturely to create publicity for firm and new leads.

```html
<!DOCTYPE html>
<html lang="en">
<head>
<meta charset="utf-8">
<title>Serenova Law Firm – Social Banners</title>
<link href="https://fonts.googleapis.com/css2?family=Cinzel:wght@600;700&family=Poppins:wght@300;500;600;700&family=Roboto:wght@400;500;700&display=swap" rel="stylesheet">
<style>
  :root{
    --board:#8a8a8a;
    --teal:#186c6e;
    --teal-deep:#135a5d;
    --navy:#2b3c4e;
    --white:#ffffff;
    --mist:#eeeeee;
    --photo-warm:#b98a5f;
    --photo-dark:#2a2f3a;
  }
  *{margin:0;padding:0;box-sizing:border-box}
  html,body{width:1200px;height:623px;overflow:hidden;background:var(--board)}
  .board{position:relative;width:1200px;height:623px;font-family:"Roboto",sans-serif}
  .platform-label{position:absolute;color:var(--white);font:700 21px "Roboto",sans-serif;transform:translateX(-50%);white-space:nowrap}
  .banner{position:absolute;overflow:hidden}
  .banner svg.art{position:absolute;left:0;top:0}
  .banner .t{position:absolute;white-space:nowrap}

  /* Chatterbox */
  .chatterbox{left:29px;top:47px;width:401px;height:176px;background:var(--teal)}
  .chatterbox .brand{left:15px;top:12px;color:var(--white);font:700 12px "Cinzel",serif;letter-spacing:.3px}
  .chatterbox .headline{left:15px;top:50px;color:var(--white);font:700 15px/21px "Cinzel",serif;letter-spacing:.4px}
  .chatterbox .intro{left:15px;top:97px;color:var(--white);font:500 5px/11px "Roboto",sans-serif}
  .chatterbox .cta-label{left:54px;top:142px;color:#cfe3e3;font:400 6.5px "Roboto",sans-serif}
  .chatterbox .cta-phone{left:54px;top:151px;color:var(--white);font:700 10px "Roboto",sans-serif}

  /* HomeLane */
  .homelane{left:29px;top:284px;width:588px;height:307px;background:var(--navy)}
  .homelane .brand{left:27px;top:33px;color:var(--white);font:700 22px "Cinzel",serif}
  .homelane .brand small{display:block;font:400 8px "Roboto",sans-serif;letter-spacing:1px;margin-top:1px}
  .homelane .lead{left:27px;top:111px;color:var(--white);font:300 25px "Poppins",sans-serif}
  .homelane .lead-strong{left:27px;top:145px;color:var(--white);font:600 26px "Poppins",sans-serif}
  .homelane .locale{left:27px;top:191px;color:var(--white);font:400 10px "Roboto",sans-serif}
  .homelane .site{left:58px;top:268px;color:var(--white);font:500 9px "Poppins",sans-serif}

  /* Picturely */
  .picturely{left:642px;top:63px;width:529px;height:529px;background:var(--white)}
  .picturely .brand{left:43px;top:28px;color:var(--navy);font:700 29px "Cinzel",serif}
  .picturely .brand small{display:block;font:400 10px "Roboto",sans-serif;letter-spacing:1px;color:var(--navy);margin-top:1px}
  .picturely .headline{left:22px;top:144px;color:var(--white);font:700 27px/41px "Cinzel",serif}
  .picturely .intro{left:22px;top:231px;color:var(--white);font:400 9px/15.2px "Roboto",sans-serif}
  .picturely .cta-label{left:209px;top:449px;color:var(--teal);font:500 15px "Roboto",sans-serif}
  .picturely .cta-phone{left:209px;top:467px;color:var(--navy);font:400 16px "Roboto",sans-serif;letter-spacing:.3px}
  .picturely .site{left:333px;top:500px;color:var(--white);font:500 10px "Poppins",sans-serif}
</style>
</head>
<body>
<div class="board">

  <div class="platform-label" style="left:229px;top:11px">Chatterbox</div>
  <div class="platform-label" style="left:322px;top:241px">HomeLane</div>
  <div class="platform-label" style="left:903px;top:20px">Picturely</div>

  <!-- Chatterbox banner -->
  <section class="banner chatterbox">
    <svg class="art" width="401" height="176" viewBox="0 0 401 176">
      <defs>
        <linearGradient id="cbPhoto" x1="0" y1="0" x2="1" y2="1">
          <stop offset="0" stop-color="#b0725a"/>
          <stop offset=".55" stop-color="#4a4a55"/>
          <stop offset="1" stop-color="var(--photo-dark)"/>
        </linearGradient>
      </defs>
      <polygon points="147,176 210,99 272,176" fill="var(--navy)"/>
      <polygon points="256,0 290,0 226,80 304,176 271,176 210,100 210,56" fill="var(--white)"/>
      <polygon points="290,0 401,0 401,176 304,176 226,80" fill="url(#cbPhoto)" role="img" aria-label="Photo of a smiling couple seated outdoors"/>
      <g fill="none" stroke="var(--white)" stroke-width="1.2">
        <rect x="16" y="146" width="17" height="15" rx="2"/>
        <line x1="16" y1="150" x2="33" y2="150"/>
        <line x1="20" y1="144" x2="20" y2="148"/>
        <line x1="29" y1="144" x2="29" y2="148"/>
        <circle cx="30" cy="158" r="3.5" fill="var(--teal)"/>
      </g>
    </svg>
    <div class="t brand">Serenova Law Firm</div>
    <div class="t headline">Estate Planning &amp;<br>Financial Planning</div>
    <div class="t intro">Estate planning and financial planning isn’t just for the ultra-wealthy.<br>We’re here to help families plan for their legacy and protect their wealth</div>
    <div class="t cta-label">Call for Appointment</div>
    <div class="t cta-phone">(555) 014 2280</div>
  </section>

  <!-- HomeLane banner -->
  <section class="banner homelane">
    <svg class="art" width="588" height="307" viewBox="0 0 588 307">
      <defs>
        <linearGradient id="hlPhoto" x1="0" y1="0" x2="0" y2="1">
          <stop offset="0" stop-color="#141414"/>
          <stop offset=".55" stop-color="#3a2a1c"/>
          <stop offset="1" stop-color="#a8652c"/>
        </linearGradient>
      </defs>
      <polygon points="302,0 534,0 329,127 387,307 239,184" fill="var(--teal)"/>
      <polygon points="239,184 329,127 387,307" fill="var(--teal-deep)"/>
      <polygon points="534,0 588,0 588,307 387,307 329,127" fill="url(#hlPhoto)" role="img" aria-label="Photo of a rolled banknote on stacked wooden blocks spelling tax"/>
      <g fill="none" stroke="var(--teal)" stroke-width="1.6">
        <circle cx="38" cy="272" r="10"/>
        <ellipse cx="38" cy="272" rx="4.5" ry="10"/>
        <line x1="28" y1="272" x2="48" y2="272"/>
        <line x1="30" y1="266" x2="46" y2="266"/>
        <line x1="30" y1="278" x2="46" y2="278"/>
      </g>
    </svg>
    <div class="t brand">Serenova<small>LAW FIRM, PLLC</small></div>
    <div class="t lead">Comprehensive</div>
    <div class="t lead-strong">Tax Planning</div>
    <div class="t locale">Melbourne, FL Estate And Financial Planning</div>
    <div class="t site">www.keepandbuildwealth.com</div>
  </section>

  <!-- Picturely post -->
  <section class="banner picturely">
    <svg class="art" width="529" height="529" viewBox="0 0 529 529">
      <defs>
        <linearGradient id="pcPhoto" x1="0" y1="0" x2="1" y2="1">
          <stop offset="0" stop-color="#e0a070"/>
          <stop offset=".45" stop-color="#efe4d8"/>
          <stop offset="1" stop-color="#2f3b52"/>
        </linearGradient>
      </defs>
      <polygon points="474,0 529,0 529,70 420,110" fill="var(--mist)"/>
      <polygon points="121,529 330,250 420,250 235,529" fill="var(--mist)"/>
      <polygon points="0,90 381,90 190,375 0,375" fill="var(--navy)"/>
      <polygon points="43,375 136,375 129,384 47,384" fill="var(--teal)"/>
      <polygon points="391,122 526,122 526,130 386,130" fill="var(--teal)"/>
      <polygon points="371,130 529,130 529,468 350,468 248,300" fill="url(#pcPhoto)" role="img" aria-label="Photo of a hand using a calculator over tax forms"/>
      <polygon points="288,487 526,487 526,525 261,525" fill="var(--teal)"/>
      <g fill="var(--teal)">
        <path d="M56 462 q19-12 39 0 l-3 7 -9-2 v-4 h-15 v4 l-9 2z"/>
        <path d="M62 471 h27 l5 17 h-37z"/>
        <circle cx="75" cy="480" r="5" fill="var(--white)"/>
        <circle cx="75" cy="480" r="2.5"/>
      </g>
      <g fill="none" stroke="var(--white)" stroke-width="1.6">
        <circle cx="313" cy="506" r="10"/>
        <ellipse cx="313" cy="506" rx="4.5" ry="10"/>
        <line x1="303" y1="506" x2="323" y2="506"/>
        <line x1="305" y1="500" x2="321" y2="500"/>
        <line x1="305" y1="512" x2="321" y2="512"/>
      </g>
    </svg>
    <div class="t brand">Serenova<small>LAW FIRM, PLLC</small></div>
    <div class="t headline">Estate Planning<br>101 Masterclass</div>
    <div class="t intro">This Webinar Is Designed For Everyone—Young Families<br>Starting Out, Empty Nesters, Former Military Personnel,<br>Unique Family Structures, And Those Worried About<br>Long-Term Care Costs.</div>
    <div class="t cta-label">Call Us Now</div>
    <div class="t cta-phone">(555) 014 2280</div>
    <div class="t site">www.keepandbuildwealth.com</div>
  </section>

</div>
</body>
</html>
```